Tall Fern Roofing Business Card

Need a business card with the logo that was designed here

Contact Information for Business Card

Name, Title, Phone, Email, Website, Company name

```html
<!DOCTYPE html>
<html lang="en">
<head>
<meta charset="utf-8">
<title>Tall Fern Roofing Business Card</title>
<link rel="stylesheet" href="https://fonts.googleapis.com/css2?family=Open+Sans:wght@400;700&display=swap">
<style>
  :root {
    --brand-blue: #1f74c0;
    --brand-grey: #8f9196;
    --ink: #2b2b2b;
    --paper: #ffffff;
    --backdrop: #d9d9d6;
  }
  * { margin: 0; padding: 0; box-sizing: border-box; }
  html, body { width: 1200px; height: 801px; overflow: hidden; }
  body {
    background: var(--backdrop);
    font-family: "Open Sans", sans-serif;
    position: relative;
  }
  .card {
    position: absolute;
    top: 246px;
    width: 540px;
    height: 309px;
    background: var(--paper);
    border-radius: 22px;
    box-shadow: 0 4px 0 var(--brand-blue), 0 14px 28px rgba(0,0,0,0.18);
    overflow: hidden;
  }
  .card--contact { left: 40px; }
  .card--front { left: 620px; }

  .wordmark {
    font-weight: 700;
    color: var(--brand-blue);
    display: flex;
    align-items: center;
    gap: 10px;
    white-space: nowrap;
  }
  .wordmark__square {
    width: 14px; height: 14px;
    background: var(--brand-blue);
    flex: none;
  }
  .card--contact .wordmark {
    position: absolute;
    left: 34px; top: 136px;
    font-size: 23px;
  }
  .card--front .wordmark {
    position: absolute;
    left: 50%; top: 50%;
    transform: translate(-50%, -50%);
    font-size: 40px;
    gap: 16px;
  }
  .card--front .wordmark__square { width: 22px; height: 22px; }

  .divider {
    position: absolute;
    left: 262px; top: 40px;
    width: 2px; height: 229px;
    background: var(--brand-blue);
  }
  .contact {
    position: absolute;
    left: 290px; top: 46px;
    color: var(--ink);
    font-size: 13px;
    line-height: 1.45;
  }
  .contact__name {
    color: var(--brand-blue);
    font-weight: 700;
    font-size: 21px;
    letter-spacing: 0.5px;
    line-height: 1.1;
  }
  .contact__title { font-size: 13px; margin-bottom: 14px; }
  .contact__address { margin-bottom: 14px; }
  .contact__row { display: flex; align-items: center; gap: 8px; }
  .contact__row svg { width: 12px; height: 12px; flex: none; }
</style>
</head>
<body>

<section class="card card--contact">
  <div class="wordmark"><span class="wordmark__square"></span>Tall Fern Roofing</div>
  <div class="divider"></div>
  <div class="contact">
    <p class="contact__name">DANA WHITLOCK</p>
    <p class="contact__title">Managing Director</p>
    <p class="contact__address">Your address, City<br>State, Zip 1234</p>
    <p class="contact__row">
      <svg viewBox="0 0 12 12"><path fill="#1f74c0" d="M2.5 1l2 2.2-1 1.2c.6 1.4 1.7 2.5 3.1 3.1l1.2-1L10 8.5 9 10.5C5 10.5 1.5 7 1.5 3z"/></svg>
      123 456 789
    </p>
    <p class="contact__row">
      <svg viewBox="0 0 12 12"><rect x="1" y="2.5" width="10" height="7" fill="#1f74c0"/><path d="M1 2.5l5 4 5-4" stroke="#fff" fill="none" stroke-width="1"/></svg>
      info@youremail.com
    </p>
    <p class="contact__row">
      <svg viewBox="0 0 12 12"><circle cx="6" cy="6" r="5" fill="#1f74c0"/><path d="M1 6h10M6 1c-2 2.5-2 7.5 0 10M6 1c2 2.5 2 7.5 0 10" stroke="#fff" fill="none" stroke-width="0.8"/></svg>
      www.yourwebsite.com
    </p>
  </div>
</section>

<section class="card card--front">
  <div class="wordmark"><span class="wordmark__square"></span>Tall Fern Roofing</div>
</section>

</body>
</html>
```